Modern Business Card for Larkwell 2018

Our company assumes the best about people. We are creating an online community of entrepreneurs and business leaders who struggle with marketing their business online.

This business card should POP! We recently got a new logo and are launching a new website next month, so our business cards should make a statement that feels:
-Fresh
-Smart
-Trustworthy
-Fun

Target Market(s)

small business owners, entrepreneurs

Industry/Entity Type

Digital Marketing

Contact Information for Business Card

Dimensions: 3.5" x 2"

Font styles to use
Sans Serif

Colors
f37122
ffffff

Requirements
Must have
• We need a business card with a modern, bold design. We will use one side of the card as a lead-generation offer, so text on one side will need to fit up to 140 characters. The business card should stick to our core colors (orange, black, and white).
Nice to have
• We think a vertical "portrait" design could be interesting.
Should not have
• Should not look like a traditional business card. The round icon should stand out from a distance.

```html
<!DOCTYPE html>
<html lang="en">
<head>
<meta charset="utf-8">
<title>Larkwell Business Card</title>
<link rel="stylesheet" href="https://fonts.googleapis.com/css2?family=Open+Sans:wght@400;700;800&display=swap">
<style>
  :root {
    --orange: #f37122;
    --white: #ffffff;
    --ink: #2b2b2b;
    --grey: #6a6a6a;
    --backdrop: #ece9e4;
    --rule: #3a3a3a;
  }
  * { box-sizing: border-box; margin: 0; padding: 0; }
  html, body {
    width: 1200px; height: 950px; overflow: hidden;
    background: var(--backdrop);
    font-family: "Open Sans", Arial, sans-serif;
  }
  .sheet {
    width: 1200px; height: 950px;
    display: flex; flex-direction: column; align-items: center; justify-content: center;
    gap: 70px;
  }
  .card {
    position: relative;
    width: 630px; height: 360px;
    border-radius: 4px;
    box-shadow: 0 2px 10px rgba(0,0,0,.12);
    overflow: hidden;
  }
  /* Front */
  .card-front { background: var(--white); }
  .brand {
    position: absolute; right: 60px; top: 52px;
    display: flex; flex-direction: column; align-items: flex-start;
  }
  .brand-dot {
    width: 38px; height: 38px; border-radius: 50%;
    background: var(--orange); margin: 0 0 12px 34px;
  }
  .brand-name {
    font-weight: 800; font-size: 44px; letter-spacing: 3px;
    color: var(--ink); line-height: 1;
  }
  .brand-tagline {
    margin-top: 8px; font-weight: 700; font-size: 12px;
    letter-spacing: 1.6px; text-transform: uppercase; color: var(--ink);
  }
  .contact {
    position: absolute; left: 44px; bottom: 40px;
  }
  .contact-name {
    font-weight: 800; font-size: 22px; color: var(--orange);
    text-transform: uppercase; letter-spacing: .5px; line-height: 1.15;
  }
  .contact-role {
    font-weight: 800; font-size: 18px; color: var(--ink);
    text-transform: uppercase; line-height: 1.2;
  }
  .contact-email { font-size: 17px; color: var(--grey); margin-top: 2px; }

  /* Back */
  .card-back { background: var(--orange); color: var(--white); }
  .offer-mark {
    position: absolute; left: 40px; top: 34px;
    width: 190px; display: flex; flex-direction: column; align-items: center; gap: 12px;
  }
  .offer-mark-circle {
    width: 130px; height: 130px; border-radius: 50%; background: var(--white);
  }
  .offer-mark-name {
    font-weight: 800; font-size: 20px; letter-spacing: 2px; color: var(--white);
  }
  .offer-divider {
    position: absolute; left: 258px; top: 30px; width: 1px; height: 180px;
    background: rgba(255,255,255,.45);
  }
  .offer {
    position: absolute; left: 282px; top: 32px; right: 30px;
  }
  .offer-headline {
    font-weight: 800; font-size: 23px; line-height: 1.08; text-transform: uppercase;
  }
  .offer-body { margin-top: 10px; font-size: 15px; line-height: 1.3; }
  .offer-url { margin-top: 8px; font-weight: 800; font-size: 19px; }
  .notes {
    position: absolute; left: 30px; right: 30px; bottom: 26px; height: 100px;
    background: var(--white); border-radius: 10px;
  }
  .notes svg { display: block; }
</style>
</head>
<body>
<main class="sheet">
  <section class="card card-front" aria-label="Card front">
    <div class="brand">
      <span class="brand-dot"></span>
      <span class="brand-name">LARKWELL</span>
      <span class="brand-tagline">Tell stories that inspire action</span>
    </div>
    <div class="contact">
      <p class="contact-name">Dana Whitlock</p>
      <p class="contact-role">Story Marketing Coach</p>
      <p class="contact-email">dana@larkwellnow.com</p>
    </div>
  </section>

  <section class="card card-back" aria-label="Card back">
    <div class="offer-mark">
      <span class="offer-mark-circle"></span>
      <span class="offer-mark-name">LARKWELL</span>
    </div>
    <span class="offer-divider"></span>
    <div class="offer">
      <p class="offer-headline">Reach more people.<br>Make more money.<br>Create more impact.</p>
      <p class="offer-body">Get your free Larkwell Starter Package and our marketing guide today at</p>
      <p class="offer-url">Larkwellnow.com/start</p>
    </div>
    <div class="notes">
      <svg width="570" height="100" viewBox="0 0 570 100" aria-hidden="true">
        <line x1="22" y1="36" x2="548" y2="36" stroke="var(--rule)" stroke-width="1"/>
        <line x1="22" y1="70" x2="548" y2="70" stroke="var(--rule)" stroke-width="1"/>
      </svg>
    </div>
  </section>
</main>
</body>
</html>
```